Design a label for a dog shampoo names fluffo, the sell point of this series of shampoo is “just like wash your dogs with milk, not harm for your hand ”, the style could be gentle or professional or even amazing.

Use only 2 colors in the design job, the color of our logo could be changed, it depends on your whole page. Please design in CDR or ai.

update:
Pls do more change with the fonts when you design the front page, including title and details. Try more styles of fonts. Addition, this design will be printed on the bottle, no a label stick on it.
Updates

Do not put a real dog or animal on the page, Pay more attention to the types of fonts

Reason: Expect for more design idea.

Target Market(s)

people 20-30 years old who have dogs and cats at home

Industry/Entity Type

It Professional

Requirements
Nice to have
• It would be nice if you add some detail words in the design of the right side.

```html
<!DOCTYPE html>
<html lang="en">
<head>
<meta charset="utf-8">
<title>Fluffo – Super Conditioning Nutrient Shampoo</title>
<link rel="stylesheet" href="https://fonts.googleapis.com/css2?family=Exo+2:ital,wght@0,600;0,800;1,300&display=swap">
<style>
  :root {
    --milk-blue: #97c8e8;
    --deep-blue: #4d8fc0;
    --paper: #ffffff;
  }
  html, body {
    margin: 0;
    padding: 0;
    width: 1200px;
    height: 2292px;
    overflow: hidden;
    background: var(--paper);
  }
  .label {
    position: relative;
    width: 1200px;
    height: 2292px;
    background: var(--paper);
    font-family: "Exo 2", sans-serif;
  }
  .brand-word {
    position: absolute;
    margin: 0;
    font-family: "Exo 2", sans-serif;
    font-weight: 800;
    color: var(--milk-blue);
    text-transform: uppercase;
    line-height: 1;
    letter-spacing: -0.02em;
  }
  .brand-word--top {
    left: 100px;
    top: 380px;
    font-size: 440px;
  }
  .brand-word--bottom {
    left: 592px;
    top: 850px;
    font-size: 440px;
  }
  .product-details {
    position: absolute;
    right: 670px;
    top: 905px;
    margin: 0;
    padding: 0;
    list-style: none;
    text-align: right;
    color: var(--deep-blue);
    font-family: "Exo 2", sans-serif;
    font-weight: 600;
    font-size: 56px;
    line-height: 100px;
    letter-spacing: 0.04em;
  }
  .product-banner {
    position: absolute;
    left: 105px;
    top: 1300px;
    width: 987px;
    height: 333px;
  }
  .product-banner svg {
    position: absolute;
    inset: 0;
    width: 100%;
    height: 100%;
  }
  .product-banner__title {
    position: absolute;
    inset: 0;
    margin: 0;
    display: flex;
    flex-direction: column;
    justify-content: center;
    align-items: center;
    color: var(--paper);
    font-family: "Exo 2", sans-serif;
    font-style: italic;
    font-weight: 300;
    font-size: 62px;
    line-height: 108px;
    letter-spacing: 0.22em;
  }
  .mascot-area {
    position: absolute;
    left: 487px;
    top: 1750px;
    width: 213px;
    height: 163px;
    background: var(--deep-blue);
    border-radius: 40px;
  }
</style>
</head>
<body>
  <main class="label">
    <h1 class="brand-word brand-word--top">Fluf</h1>
    <p class="brand-word brand-word--bottom" aria-hidden="true">Fo</p>

    <ul class="product-details">
      <li>moisture rich</li>
      <li>smooth &amp; silky</li>
      <li>1000ml</li>
    </ul>

    <section class="product-banner">
      <svg viewBox="0 0 987 333" preserveAspectRatio="none" aria-hidden="true">
        <path fill="var(--deep-blue)" d="M40 40 C80 5 150 15 200 25 C260 5 330 10 390 22 C450 5 520 8 580 20 C640 4 720 6 780 18 C840 2 910 10 950 30 C985 55 975 95 970 130 C985 165 985 200 975 240 C985 280 960 320 910 318 C850 330 780 325 720 315 C660 330 590 328 530 318 C470 332 400 330 340 320 C280 333 200 330 140 320 C80 330 30 315 15 280 C5 245 10 210 5 175 C0 140 10 110 8 80 C8 60 20 50 40 40 Z"/>
      </svg>
      <h2 class="product-banner__title">
        <span>super conditioning</span>
        <span>nutrient shampoo</span>
      </h2>
    </section>

    <div class="mascot-area" role="img" aria-label="Small sitting dog silhouette mascot"></div>
  </main>
</body>
</html>
```